Simple and Clean business card design

We would like the design to be simple clean and to incorporate our colors.

We are open to your design and talent, we have the dots in our logo as we think of it as data points and we connect data points for people.

We are open to see the great creative and clean design you bring to the table

Contact Information for Business Card

please include: name, position, email, phone and website

Font styles to use
Sans Serif

Requirements
Must have
• my colors incorporated, simplicity
Nice to have
• lots of white space, simplicity
Should not have
• complexicity/ complex art

```html
<!DOCTYPE html>
<html lang="en">
<head>
<meta charset="utf-8">
<title>Tessaly business card</title>
<link rel="stylesheet" href="https://fonts.googleapis.com/css2?family=Lato:wght@700&family=Roboto:wght@400&display=swap">
<style>
  :root {
    --backdrop: #737373;
    --card-light: #ffffff;
    --card-dark: #1b1b1b;
    --ink: #111111;
    --paper-ink: #ffffff;
    --brand-blue: #4285f4;
    --brand-green: #34a853;
    --brand-yellow: #fbbc05;
    --brand-red: #ea4335;
  }
  html, body {
    margin: 0;
    padding: 0;
    width: 1065px;
    height: 1200px;
    overflow: hidden;
    background: var(--backdrop);
  }
  .stage {
    position: relative;
    width: 1065px;
    height: 1200px;
  }
  .card {
    position: absolute;
    width: 583px;
    height: 362px;
    box-shadow: 3px 4px 5px rgba(0, 0, 0, 0.55);
  }
  .card--front {
    left: 292px;
    top: 218px;
    background: var(--card-light);
    border-radius: 0 181px 181px 0;
  }
  .card--back {
    left: 263px;
    top: 623px;
    background: var(--card-dark);
    border-radius: 181px 0 0 181px;
  }
  .person {
    position: absolute;
    left: 37px;
    top: 85px;
  }
  .person__name {
    margin: 0;
    font-family: "Lato", sans-serif;
    font-weight: 700;
    font-size: 26px;
    line-height: 30px;
    color: var(--ink);
  }
  .person__role {
    margin: 0;
    font-family: "Roboto", sans-serif;
    font-size: 17px;
    line-height: 20px;
    color: var(--brand-blue);
  }
  .contacts {
    position: absolute;
    left: 37px;
    top: 198px;
    margin: 0;
    padding: 0;
    list-style: none;
  }
  .contacts__item {
    display: flex;
    align-items: center;
    height: 20px;
    margin-bottom: 4.5px;
    font-family: "Roboto", sans-serif;
    font-size: 17px;
    color: var(--ink);
  }
  .contacts__icon {
    width: 20px;
    height: 20px;
    margin-right: 5px;
    flex: none;
  }
  .contacts__accent { color: var(--brand-blue); }
  .wordmark {
    position: absolute;
    display: flex;
    align-items: center;
    gap: 10px;
    font-family: "Lato", sans-serif;
    font-weight: 700;
    font-size: 58px;
    line-height: 1;
    letter-spacing: 0.5px;
  }
  .wordmark__dot {
    width: 16px;
    height: 16px;
    border-radius: 50%;
    background: var(--brand-blue);
    flex: none;
  }
  .card--front .wordmark {
    left: 290px;
    top: 135px;
    color: var(--ink);
  }
  .card--back .wordmark {
    left: 170px;
    top: 160px;
    color: var(--paper-ink);
  }
</style>
</head>
<body>
<main class="stage">
  <section class="card card--front" aria-label="Card front">
    <div class="person">
      <p class="person__name">Daniel Reyes</p>
      <p class="person__role">Founder/ CEO</p>
    </div>
    <ul class="contacts">
      <li class="contacts__item">
        <svg class="contacts__icon" viewBox="0 0 20 20" aria-hidden="true">
          <circle cx="10" cy="10" r="10" fill="var(--brand-green)"/>
          <path d="M6.3 5.2l2 2-1 1.3c.7 1.5 1.7 2.5 3.2 3.2l1.3-1 2 2-1.2 1.6c-3.8-.4-7-3.6-7.5-7.5z" fill="#fff"/>
        </svg>
        555-214-0198
      </li>
      <li class="contacts__item">
        <svg class="contacts__icon" viewBox="0 0 20 20" aria-hidden="true">
          <circle cx="10" cy="10" r="10" fill="var(--brand-yellow)"/>
          <rect x="5" y="6.5" width="10" height="7" fill="none" stroke="#fff" stroke-width="1.1"/>
          <path d="M5 6.5l5 4 5-4M5 13.5l3.6-3.5M15 13.5l-3.6-3.5" fill="none" stroke="#fff" stroke-width="1"/>
        </svg>
        daniel.reyes@tessaly.io
      </li>
      <li class="contacts__item">
        <svg class="contacts__icon" viewBox="0 0 20 20" aria-hidden="true">
          <circle cx="10" cy="10" r="10" fill="var(--brand-red)"/>
          <g fill="none" stroke="#fff" stroke-width="0.9">
            <circle cx="10" cy="10" r="5.2"/>
            <ellipse cx="10" cy="10" rx="2.3" ry="5.2"/>
            <path d="M4.8 10h10.4M5.6 7.5h8.8M5.6 12.5h8.8"/>
          </g>
        </svg>
        <span>www.<span class="contacts__accent">Tessaly</span>.io</span>
      </li>
    </ul>
    <div class="wordmark">
      <span class="wordmark__dot"></span>
      <span>Tessaly</span>
    </div>
  </section>

  <section class="card card--back" aria-label="Card back">
    <div class="wordmark">
      <span class="wordmark__dot"></span>
      <span>Tessaly</span>
    </div>
  </section>
</main>
</body>
</html>
```